Business card for denture clinic Veltrimora

We need a new business card with our new logo. We are a denture clinic in New Zealand with our target market being 45+ years old. We would need a space on the back to write our patients next appointment on. We would space for only one appointment rather than a list. We will attach a photo showing an example of this. But of course, we would like to see your twist on this. We want it to be bold and easy to read and a good mixture of professional but modern. We have attached our logo to be used on the card.

Target Market(s)

People aged 45+ needing dentures

Industry/Entity Type

Dental

Contact Information for Business Card

We want our logo on the front and the space to write an appointment on the back. I've attached an example our our old business card showing this. We need to have the technicians details on the front.

Font styles to use
Sans Serif

Colors
0255a3
919191
fbfbfb

Requirements
Must have
• The following details:
• Liam Dorsett BDT, PGDipCDentTech Calverin
• Dental Prosthetist
• Phone numbers: 0800 47 3125
• 09 572 1394
• Email: liam@veltrimora.co.nz
• www.veltrimora.co.nz
• Address: 14 Marlow Crest Road
• Halbrook West
• Auckland 0793
Nice to have
• We would like our business cards to have more than just two colours as we want them to be more vibrant. We have uploaded an example of a business card we liked that showed this.

```html
<!DOCTYPE html>
<html lang="en">
<head>
<meta charset="utf-8">
<title>Veltrimora – Business Card</title>
<link href="https://fonts.googleapis.com/css2?family=Montserrat:ital,wght@0,400;0,500;0,700;1,400&display=swap" rel="stylesheet">
<style>
  :root{
    --blue:#0255a3;
    --grey:#919191;
    --text:#666a70;
    --ink:#2c2f33;
    --paper:#fbfbfb;
    --accent:#f39a1e;
    --stage:#e6e7e9;
  }
  *{box-sizing:border-box;margin:0;padding:0}
  html,body{width:1200px;height:864px;overflow:hidden}
  body{
    background:var(--stage);
    font-family:'Montserrat',sans-serif;
    display:flex;flex-direction:column;align-items:center;justify-content:center;gap:28px;
  }
  .card{
    position:relative;width:680px;height:388px;background:var(--paper);
    border-radius:26px;box-shadow:0 8px 24px rgba(0,0,0,.12);overflow:hidden;
  }
  .brand{position:absolute;top:44px;right:44px;display:flex;align-items:center;gap:12px}
  .brand-square{width:34px;height:34px;background:var(--blue);border-radius:4px}
  .brand-name{font-weight:700;font-size:30px;letter-spacing:1px;color:var(--blue);text-transform:uppercase}

  /* appointment side */
  .appt-title{position:absolute;left:44px;top:122px;font-weight:700;font-size:22px;color:var(--blue)}
  .appt-rule{position:absolute;left:330px;right:44px;top:146px;height:1px;background:var(--grey)}
  .field-row{position:absolute;left:44px;right:44px;display:flex;align-items:flex-end;gap:12px;font-size:17px;color:var(--text)}
  .field-row.name{top:186px}
  .field-row.date{top:232px}
  .blank{flex:1;border-bottom:1px solid var(--grey);height:18px}
  .blank.short{flex:0 0 200px}
  .check{display:inline-flex;align-items:center;gap:7px;font-size:17px;color:var(--text)}
  .box{width:15px;height:15px;border:2px solid var(--accent);display:inline-block}
  .days{position:absolute;left:44px;right:44px;top:282px;display:flex;justify-content:space-between}
  .notice{position:absolute;left:44px;bottom:36px;font-style:italic;font-size:12.5px;color:var(--text)}

  /* technician side */
  .person{position:absolute;left:44px;top:138px}
  .person-name{font-weight:700;font-size:30px;color:var(--ink)}
  .person-cred{font-size:18px;color:var(--blue);margin-top:4px}
  .person-role{font-size:18px;color:var(--text);margin-top:4px}
  .divider{position:absolute;left:44px;right:44px;top:246px;height:1.5px;background:var(--blue)}
  .contacts{position:absolute;left:44px;top:264px;list-style:none}
  .contacts li{display:flex;align-items:center;gap:10px;font-size:17px;color:var(--text);line-height:27px}
  .contacts svg{width:17px;height:17px;flex:none}
  .address{position:absolute;right:44px;top:270px;text-align:right;font-size:17px;line-height:26px;color:var(--text)}
</style>
</head>
<body>

<section class="card card-appointment">
  <div class="brand"><span class="brand-square"></span><span class="brand-name">Veltrimora</span></div>
  <h2 class="appt-title">Your Next Appointment</h2>
  <div class="appt-rule"></div>
  <div class="field-row name">
    <span>Name</span><span class="blank"></span>
    <span>Time</span><span class="blank short"></span>
    <span class="check"><span class="box"></span>AM</span>
    <span class="check"><span class="box"></span>PM</span>
  </div>
  <div class="field-row date">
    <span>Date</span><span class="blank"></span>
  </div>
  <div class="days">
    <span class="check"><span class="box"></span>Mon</span>
    <span class="check"><span class="box"></span>Tues</span>
    <span class="check"><span class="box"></span>Wed</span>
    <span class="check"><span class="box"></span>Thu</span>
    <span class="check"><span class="box"></span>Fri</span>
  </div>
  <p class="notice">If you are unable to keep your appointment please call the office 24 hours in advance.</p>
</section>

<section class="card card-technician">
  <div class="brand"><span class="brand-square"></span><span class="brand-name">Veltrimora</span></div>
  <div class="person">
    <h1 class="person-name">Liam Dorsett</h1>
    <p class="person-cred">BDT, PGDipCDentTech Calverin</p>
    <p class="person-role">Dental Prosthetist</p>
  </div>
  <div class="divider"></div>
  <ul class="contacts">
    <li><svg viewBox="0 0 24 24"><path fill="var(--accent)" d="M6.6 10.8a15.1 15.1 0 0 0 6.6 6.6l2.2-2.2a1 1 0 0 1 1-.25 11.4 11.4 0 0 0 3.6.57 1 1 0 0 1 1 1V20a1 1 0 0 1-1 1A17 17 0 0 1 3 4a1 1 0 0 1 1-1h3.5a1 1 0 0 1 1 1c0 1.25.2 2.45.57 3.57a1 1 0 0 1-.25 1z"/></svg>0800 47 3125</li>
    <li><svg viewBox="0 0 24 24"><path fill="var(--accent)" d="M6.6 10.8a15.1 15.1 0 0 0 6.6 6.6l2.2-2.2a1 1 0 0 1 1-.25 11.4 11.4 0 0 0 3.6.57 1 1 0 0 1 1 1V20a1 1 0 0 1-1 1A17 17 0 0 1 3 4a1 1 0 0 1 1-1h3.5a1 1 0 0 1 1 1c0 1.25.2 2.45.57 3.57a1 1 0 0 1-.25 1z"/></svg>09 572 1394</li>
    <li><svg viewBox="0 0 24 24"><rect x="2" y="5" width="20" height="14" rx="1.5" fill="var(--accent)"/><path d="M3 6l9 7 9-7" fill="none" stroke="var(--paper)" stroke-width="1.6"/></svg>liam@veltrimora.co.nz</li>
    <li><svg viewBox="0 0 24 24"><circle cx="12" cy="12" r="10" fill="var(--accent)"/><g fill="none" stroke="var(--paper)" stroke-width="1.3"><ellipse cx="12" cy="12" rx="4.5" ry="10"/><path d="M2 12h20M4 7h16M4 17h16"/></g></svg>www.veltrimora.co.nz</li>
  </ul>
  <address class="address" style="font-style:normal">14 Marlow Crest Road<br>Halbrook West<br>Auckland 0793</address>
</section>

</body>
</html>
```